Harborline Renewal Business Card Design

Professional and clean design. The design colors should flow with the logo. Two-sided card with the website on the back which is:

www.HarborlineRenewal.example.

"Specializing in Water Damage Restoration"

On the front I need the name, email, phone, and logo.

Name: Darnell Quisby
Email: Darnell@HarborlineRenewal.example
Phone: 555-318-2046 for now

I only have the Preview and Thumbnail right now but should have the source files uploaded within a day or two.

Target Market(s)

Flood victims, home owners with water damage from busted pipes etc...

Industry/Entity Type

Business

Contact Information for Business Card

Name: Darnell Quisby

Font styles to use
Serif
Sans Serif

Requirements
Must have
• Business Card Details Info

```html
<!DOCTYPE html>
<html lang="en">
<head>
<meta charset="UTF-8">
<title>Harborline Renewal Business Card</title>
<link rel="stylesheet" href="https://fonts.googleapis.com/css2?family=Cinzel:wght@600&family=Open+Sans:wght@400;600;700&display=swap">
<style>
  :root {
    --backdrop: #3b3330;
    --card: #0c0c0d;
    --card-edge: #1c1c1e;
    --brand-blue: #3aa3e3;
    --brand-light: #58c2f2;
    --text-white: #f2f2f2;
    --divider: #1f1f22;
  }
  * { margin: 0; padding: 0; box-sizing: border-box; }
  html, body {
    width: 1200px; height: 900px; overflow: hidden;
    background: var(--backdrop);
  }
  .canvas {
    position: relative; width: 1200px; height: 900px;
    display: flex; align-items: center; justify-content: center; gap: 50px;
  }
  .card {
    position: relative; width: 520px; height: 300px;
    background: var(--card);
    border: 1px solid var(--card-edge);
    box-shadow: 0 14px 30px rgba(0,0,0,0.45);
  }

  /* Front: contact side */
  .card-front { display: flex; }
  .front-brand {
    width: 230px; height: 100%;
    display: flex; flex-direction: column; align-items: center; justify-content: center; gap: 14px;
    border-right: 1px solid var(--divider);
  }
  .brand-dot {
    width: 120px; height: 120px; border-radius: 50%;
    background: var(--brand-blue);
  }
  .brand-name {
    font-family: "Cinzel", serif; font-weight: 600;
    color: var(--brand-blue); letter-spacing: 1px;
    text-transform: uppercase; text-align: center;
  }
  .front-brand .brand-name { font-size: 15px; }
  .contact {
    flex: 1; padding: 0 24px;
    display: flex; flex-direction: column; justify-content: center;
    font-family: "Open Sans", sans-serif;
  }
  .contact-name {
    color: var(--brand-blue); font-weight: 700; font-size: 20px;
    margin-bottom: 18px;
  }
  .contact-line {
    display: flex; align-items: center; gap: 8px;
    color: var(--text-white); font-size: 14px; margin-bottom: 6px;
    white-space: nowrap;
  }
  .contact-line svg { flex: none; }

  /* Back: brand side */
  .card-back {
    display: flex; flex-direction: column; align-items: center; justify-content: center;
    text-align: center;
  }
  .card-back .brand-dot { width: 70px; height: 70px; margin-bottom: 14px; }
  .card-back .brand-name { font-size: 34px; line-height: 1.1; margin-bottom: 22px; }
  .website {
    font-family: "Open Sans", sans-serif; font-size: 13px;
    color: var(--text-white); margin-bottom: 30px;
  }
  .tagline {
    font-family: "Open Sans", sans-serif; font-size: 14px; font-weight: 400;
    color: var(--brand-light); text-transform: uppercase; letter-spacing: 0.3px;
  }
</style>
</head>
<body>
<main class="canvas">
  <section class="card card-front" aria-label="Card front">
    <div class="front-brand">
      <span class="brand-dot" aria-hidden="true"></span>
      <span class="brand-name">Harborline Renewal</span>
    </div>
    <div class="contact">
      <p class="contact-name">Darnell Quisby</p>
      <p class="contact-line">
        <svg width="12" height="12" viewBox="0 0 24 24" aria-hidden="true"><path fill="#f2f2f2" d="M6.6 10.8a15 15 0 0 0 6.6 6.6l2.2-2.2a1 1 0 0 1 1-.25 11.4 11.4 0 0 0 3.6.57 1 1 0 0 1 1 1V20a1 1 0 0 1-1 1A17 17 0 0 1 3 4a1 1 0 0 1 1-1h3.5a1 1 0 0 1 1 1c0 1.25.2 2.45.57 3.57a1 1 0 0 1-.25 1z"/></svg>
        555-318-2046
      </p>
      <p class="contact-line">
        <svg width="12" height="10" viewBox="0 0 24 18" aria-hidden="true"><rect x="0" y="0" width="24" height="18" rx="2" fill="#f2f2f2"/><path d="M1 1l11 8 11-8" stroke="#0c0c0d" stroke-width="2" fill="none"/></svg>
        Darnell@HarborlineRenewal.example
      </p>
    </div>
  </section>

  <section class="card card-back" aria-label="Card back">
    <span class="brand-dot" aria-hidden="true"></span>
    <h1 class="brand-name">Harborline<br>Renewal</h1>
    <p class="website">www.HarborlineRenewal.example</p>
    <p class="tagline">Specializing in Water Damage Restoration</p>
  </section>
</main>
</body>
</html>
```